Business cards - BRENT Roofing & Siding

We need simple business cards made up for our Roofing & Siding business based in Calgary Alberta.
The logo on one side of the card and potentially our slogan "Built with trust, verified by time".
The other side could have:
-A small logo
-Rep name:
-Rep cell phone:
-Rep email:
-Office phone: 403-684-2093
-Website: PrairieShingleWorks.com

We would like to incorporate the colours from our logo, especially the lite blue on the jpeg file. I have attached the ai file and jpeg file. We like the colours better on the jpeg file.

I do not require a money back guarantee

```html
<!DOCTYPE html>
<html lang="en">
<head>
<meta charset="utf-8">
<title>BRENT Roofing &amp; Siding – Business Cards</title>
<link href="https://fonts.googleapis.com/css2?family=Montserrat:wght@400;500;700&display=swap" rel="stylesheet">
<style>
  :root {
    --page-bg: #e9e9e9;
    --card-bg: #1e1e1e;
    --emboss: #333333;
    --white: #ffffff;
    --sky-blue: #1e88e5;
    --text-light: #f2f2f2;
  }
  * { box-sizing: border-box; margin: 0; padding: 0; }
  html, body {
    width: 1200px; height: 900px; overflow: hidden;
    background: var(--page-bg);
    font-family: "Montserrat", sans-serif;
  }
  .canvas { position: relative; width: 1200px; height: 900px; }
  .card {
    position: absolute;
    width: 620px; height: 354px;
    background: var(--card-bg);
    box-shadow: 0 6px 18px rgba(0,0,0,.25);
    overflow: hidden;
  }
  .card--front { left: 110px; top: 70px; }
  .card--back { left: 470px; top: 476px; }

  .wordmark {
    display: flex; align-items: center; gap: 12px;
    font-weight: 700; text-transform: uppercase;
  }
  .wordmark__square { flex: none; }
  .wordmark__name { display: block; }

  .card--front .wordmark {
    position: absolute; left: 50%; top: 50%;
    transform: translate(-50%, -50%);
    font-size: 30px; letter-spacing: 2px; color: var(--emboss);
    white-space: nowrap;
  }
  .card--front .wordmark__square { width: 16px; height: 16px; background: var(--emboss); }

  .card--back .wordmark {
    position: absolute; left: 40px; top: 50%;
    transform: translateY(-50%);
    width: 280px;
    font-size: 18px; letter-spacing: 1.5px; line-height: 26px;
    color: var(--white);
  }
  .card--back .wordmark__square { width: 16px; height: 16px; background: var(--white); }

  .divider {
    position: absolute; left: 348px; top: 102px;
    width: 2px; height: 150px; background: var(--sky-blue);
  }
  .contact { position: absolute; left: 370px; top: 94px; width: 235px; }
  .contact__name {
    font-size: 22px; font-weight: 700; color: var(--sky-blue);
    text-transform: uppercase; letter-spacing: .5px; line-height: 28px;
    white-space: nowrap;
  }
  .contact__title {
    font-size: 14px; font-weight: 500; color: var(--text-light);
    text-transform: uppercase; margin-bottom: 10px;
  }
  .contact__list { list-style: none; }
  .contact__item {
    display: flex; align-items: center; gap: 8px;
    font-size: 14px; color: var(--text-light); line-height: 24px;
    white-space: nowrap;
  }
  .contact__icon { width: 12px; height: 12px; flex: none; }
</style>
</head>
<body>
<main class="canvas">
  <section class="card card--front" aria-label="Card front">
    <div class="wordmark"><span class="wordmark__square"></span><span class="wordmark__name">BRENT Roofing &amp; Siding</span></div>
  </section>

  <section class="card card--back" aria-label="Card back">
    <div class="wordmark"><span class="wordmark__square"></span><span class="wordmark__name">BRENT<br>Roofing &amp; Siding</span></div>
    <div class="divider"></div>
    <div class="contact">
      <p class="contact__name">Dana Whitfield</p>
      <p class="contact__title">Director</p>
      <ul class="contact__list">
        <li class="contact__item">
          <svg class="contact__icon" viewBox="0 0 12 12"><path d="M2.5 1 L4.5 1 L5 3.5 L3.8 4.4 Q5 7 7.6 8.2 L8.5 7 L11 7.5 L11 9.5 Q10.5 11 9 11 Q1 10 1 3 Q1 1.5 2.5 1Z" fill="#1e88e5"/></svg>
          403-684-2093
        </li>
        <li class="contact__item">
          <svg class="contact__icon" viewBox="0 0 12 12"><rect x="3" y="0.8" width="6" height="10.4" rx="1" fill="none" stroke="#1e88e5" stroke-width="1.3"/><circle cx="6" cy="9.2" r=".7" fill="#1e88e5"/></svg>
          905-412-3378
        </li>
        <li class="contact__item">
          <svg class="contact__icon" viewBox="0 0 12 12"><rect x="0.8" y="2.3" width="10.4" height="7.4" fill="none" stroke="#1e88e5" stroke-width="1.2"/><path d="M1 2.6 L6 6.6 L11 2.6" fill="none" stroke="#1e88e5" stroke-width="1.2"/></svg>
          brentroof@northmail.net
        </li>
        <li class="contact__item">
          <svg class="contact__icon" viewBox="0 0 12 12"><circle cx="6" cy="6" r="5" fill="none" stroke="#1e88e5" stroke-width="1.1"/><ellipse cx="6" cy="6" rx="2.2" ry="5" fill="none" stroke="#1e88e5" stroke-width="1"/><path d="M1 6 H11" stroke="#1e88e5" stroke-width="1"/></svg>
          prairieshingleworks.com
        </li>
      </ul>
    </div>
  </section>
</main>
</body>
</html>
```